Agriculture Business Card

I want to use my existing logo and use my tagline of "Don't Guess...Soil Test" on the card. Looking for a double sided card that will really get peoples attention.
Contact Info:
Marlow Field Crop Edge
Calvin Brusk
2917 K Lane
Larkin, NE 68593
402-555-0193
calvin.r.brusk@fieldmailbox.net

```html
<!DOCTYPE html>
<html lang="en">
<head>
<meta charset="utf-8">
<title>Marlow Field Crop Edge – Business Card</title>
<link href="https://fonts.googleapis.com/css2?family=Montserrat:wght@400;500;700;800&display=swap" rel="stylesheet">
<style>
  :root {
    --page: #e9eaec;
    --card-white: #ffffff;
    --card-black: #1a1a1b;
    --green: #38b04a;
    --gold: #fbb21d;
    --brown: #8a5538;
    --ink: #1c1c1c;
  }
  * { box-sizing: border-box; margin: 0; padding: 0; }
  html, body {
    width: 1200px; height: 900px; overflow: hidden;
    background: var(--page);
    font-family: "Montserrat", sans-serif;
  }
  .sheet {
    width: 1200px; height: 900px;
    display: flex; flex-direction: column; align-items: center; justify-content: center;
    gap: 56px;
  }
  .card {
    position: relative;
    width: 588px; height: 336px;
    border-radius: 22px;
    overflow: hidden;
    box-shadow: 0 10px 28px rgba(0,0,0,.18);
  }
  .card--front { background: var(--card-white); }
  .card--back {
    background: var(--card-black);
    display: flex; flex-direction: column; align-items: center; justify-content: center;
    gap: 26px;
  }

  .front-swoosh { position: absolute; inset: 0; width: 100%; height: 100%; }

  .brand {
    position: absolute; left: 40px; top: 62px; width: 200px;
    display: flex; flex-direction: column; align-items: center; gap: 12px;
  }
  .brand__dot { width: 52px; height: 52px; border-radius: 50%; background: var(--gold); }
  .brand__name {
    color: var(--brown); font-weight: 800; font-size: 16px; line-height: 1.15;
    text-align: center;
  }
  .divider {
    position: absolute; left: 266px; top: 70px;
    width: 2px; height: 150px; background: var(--gold);
  }
  .contact { position: absolute; left: 296px; top: 84px; color: var(--ink); }
  .contact__name {
    color: var(--green); font-weight: 800; font-size: 27px; letter-spacing: .5px;
    text-transform: uppercase; margin-bottom: 14px;
  }
  .contact__line { font-size: 13.5px; font-weight: 500; line-height: 1.35; }
  .contact__address { margin-bottom: 12px; }
  .contact__row { display: flex; align-items: center; gap: 6px; }
  .contact__icon { width: 11px; height: 11px; flex: none; }

  .back-brand { display: flex; align-items: center; gap: 18px; }
  .back-brand__dot { width: 64px; height: 64px; border-radius: 50%; background: var(--green); }
  .back-brand__name { color: var(--gold); font-weight: 800; font-size: 30px; line-height: 1.15; }
  .tagline {
    color: var(--card-white); font-weight: 700; font-size: 17px; letter-spacing: 1.5px;
    text-transform: uppercase;
  }
  .tagline__accent { color: var(--green); }
</style>
</head>
<body>
<main class="sheet">
  <section class="card card--front" aria-label="Business card front">
    <svg class="front-swoosh" viewBox="0 0 588 336" preserveAspectRatio="none" aria-hidden="true">
      <path d="M0 168 C 120 250, 320 300, 588 306 L588 336 L0 336 Z" fill="var(--green)"/>
      <path d="M70 198 C 200 262, 380 296, 588 298 L588 306 C 380 304, 200 272, 70 198 Z" fill="var(--gold)"/>
    </svg>
    <div class="brand">
      <span class="brand__dot"></span>
      <p class="brand__name">Marlow Field<br>Crop Edge</p>
    </div>
    <span class="divider"></span>
    <div class="contact">
      <h1 class="contact__name">Calvin Brusk</h1>
      <p class="contact__line contact__address">2917 K Lane<br>Larkin, NE 68593</p>
      <p class="contact__line contact__row">
        <svg class="contact__icon" viewBox="0 0 24 24" aria-hidden="true"><path fill="var(--green)" d="M6.6 10.8a15 15 0 0 0 6.6 6.6l2.2-2.2a1 1 0 0 1 1-.25 11.4 11.4 0 0 0 3.6.57 1 1 0 0 1 1 1V20a1 1 0 0 1-1 1A17 17 0 0 1 3 4a1 1 0 0 1 1-1h3.5a1 1 0 0 1 1 1c0 1.25.2 2.45.57 3.6a1 1 0 0 1-.25 1z"/></svg>
        402-555-0193
      </p>
      <p class="contact__line contact__row">
        <svg class="contact__icon" viewBox="0 0 24 24" aria-hidden="true"><rect x="2" y="5" width="20" height="14" rx="2" fill="var(--green)"/><path d="M3 6l9 7 9-7" fill="none" stroke="#fff" stroke-width="2"/></svg>
        calvin.r.brusk@fieldmailbox.net
      </p>
    </div>
  </section>

  <section class="card card--back" aria-label="Business card back">
    <div class="back-brand">
      <span class="back-brand__dot"></span>
      <p class="back-brand__name">Marlow Field<br>Crop Edge</p>
    </div>
    <p class="tagline">Don't Guess…<span class="tagline__accent">Soil Test</span></p>
  </section>
</main>
</body>
</html>
```